Klassisches Visitenkarten-Design mit braunen Farbtönen gesucht
Zielgruppe
Meine Firma bietet Pferdezahnbehandlungen, Pferdefütterungsberatung sowie Trensen- und Gebissanpassungen an. Ausserdem habe ich eine mobile Pferdewaage. Meine Kunden sind Pferdebesitzer der gehobenen Klasse, die gerne Geld in die Hand nehmen um ihr Tier korrekt zu halten/versorgen.
Ich setze bisher auf ein klassisches Design in braun Tönen.
Aufgabenstellung
Mir ist eine klare, schnörkellose Botschaft wichtig.
Ich möchte mich gerne mit klassischem, aber auch sehr schönem Design von der Konkurrenz abheben.
Der Fokus soll auf der wissenschaftlichen Arbeitsweise mit dem Partner Pferd liegen.
Im Anhang sind Fotos von der alten Visitenkarten. Dort fehlt mir aber die klare Linie.
Normalerweise arbeite ich mit der Schriftart Eurostyle, bin aber auch für neue Vorschläge offen.

```html
<!DOCTYPE html>
<html lang="de">
<head>
<meta charset="utf-8">
<title>Visitenkarte EQUISANO</title>
<link rel="stylesheet" href="https://fonts.googleapis.com/css2?family=Exo+2:wght@400;700&display=swap">
<style>
  :root {
    --canvas-bg: #ededed;
    --card-white: #ffffff;
    --brown-dark: #552e12;
    --brown-mid: #7a4c24;
    --text-light: #ffffff;
  }
  * { margin: 0; padding: 0; box-sizing: border-box; }
  html, body {
    width: 1200px; height: 1200px; overflow: hidden;
    background: var(--canvas-bg);
    font-family: "Exo 2", Arial, sans-serif;
  }
  .canvas { position: relative; width: 1200px; height: 1200px; }
  .card {
    position: absolute; left: 240px; width: 727px; height: 470px;
  }
  .card--front { top: 81px; background: var(--card-white); color: var(--brown-dark); }
  .card--back { top: 647px; background: var(--brown-dark); color: var(--text-light); }

  .brand-mark {
    position: absolute; display: flex; align-items: center; justify-content: center; gap: 10px;
    font-weight: 700; letter-spacing: 0.04em;
  }
  .brand-mark__dot { width: 14px; height: 14px; border-radius: 50%; background: currentColor; }
  .card--front .brand-mark { left: 26px; top: 30px; width: 225px; height: 350px; font-size: 30px; }
  .card--back .brand-mark { left: 197px; top: 33px; width: 333px; height: 332px; font-size: 44px; }

  .contact {
    position: absolute; right: 41px; top: 100px; text-align: right;
  }
  .contact__name { font-size: 26px; font-weight: 700; line-height: 1.1; }
  .contact__role { margin-top: 22px; font-size: 20px; font-weight: 700; line-height: 1.15; }
  .contact__address, .contact__lines { font-size: 20px; font-weight: 400; line-height: 1.2; }
  .contact__address { margin-top: 18px; }
  .contact__lines { margin-top: 22px; }

  .services {
    position: absolute; font-size: 18px; font-weight: 700; white-space: nowrap;
  }
  .card--front .services { right: 41px; top: 399px; }
  .card--back .services { left: 0; right: 0; top: 395px; text-align: center; }
</style>
</head>
<body>
<div class="canvas">
  <section class="card card--front">
    <div class="brand-mark"><span class="brand-mark__dot"></span>EQUISANO</div>
    <div class="contact">
      <p class="contact__name">Miriam L. Hagedorn</p>
      <p class="contact__role">Agrarwissenschaften (Dr. sc.)<br>EQUISANO</p>
      <p class="contact__address">Lindenweg 12<br>79999 Tannau/Südschwarzwald</p>
      <p class="contact__lines">Telefon: +49 (0) 170 - 5550123<br>E-Mail: praxis@equisano-mail.de<br>Internet: www.equisano.de</p>
    </div>
    <p class="services">Pferdezahnbehandlung * Pferdefütterungsberatung * Pferdewaage</p>
  </section>

  <section class="card card--back">
    <div class="brand-mark"><span class="brand-mark__dot"></span>EQUISANO</div>
    <p class="services">Pferdezahnbehandlung * Pferdefütterungsberatung * Pferdewaage</p>
  </section>
</div>
</body>
</html>
```